Norrell Advisory WA Business Card

Create an interesting, eye catching and colourful two sided business card. We are a business consulting operation assisting SME's improve all areas of their business. We provide consulting services to assist SME's to create a culture of continuous improvement, making a positive difference in the business. Our tag line is Small changes, big rewards. We want to create a well recognised, innovative brand that can be continued throughout our website, social media and email correspondence.

Target Market(s)

Small to Medium Enterprise Business Owners

Industry/Entity Type

Business Consultant

Contact Information for Business Card

Name of Business: Norrell Advisory - Small Changes Big Rewards
Derek Holloway Ph 0407385510 Megan Holloway Ph 0407913847
Email norrelladvisorywa@mailbox-example.com
Web address TBA
FaceBook page TBA

BACKSIDE OF CARD

Providing assistance with:

• Organisation & Efficiency
• Revenue generation & Marketing
• Financial Management
• Production quality & delivery
• Systems & Process documentation
• Exit Strategy

Font styles to use
Other font styles liked:
• Calibri

Colors

Designer to choose colors to be used in the design.

Requirements
Must have
• Calibri font

```html
<!DOCTYPE html>
<html lang="en">
<head>
<meta charset="utf-8">
<title>Norrell Advisory WA – Business Card</title>
<link rel="stylesheet" href="https://fonts.googleapis.com/css2?family=Carlito:wght@400;700&family=Oswald:wght@500;600&display=swap">
<style>
  :root {
    --backdrop: #3b3430;
    --card: #0e0e0e;
    --rule: #4a4a4a;
    --white: #f2f2f2;
    --silver: #c9c9c9;
    --text-soft: #d6d6d6;
    --green: #7cc142;
    --blue: #2a8fd8;
  }
  * { box-sizing: border-box; margin: 0; padding: 0; }
  html, body { width: 1200px; height: 844px; overflow: hidden; }
  body {
    background: var(--backdrop);
    font-family: "Carlito", "Calibri", sans-serif;
    position: relative;
  }
  .card {
    position: absolute;
    top: 272px;
    width: 525px;
    height: 300px;
    background: var(--card);
    box-shadow: 0 10px 30px rgba(0,0,0,.45);
    overflow: hidden;
  }
  .card--front { left: 50px; }
  .card--back { left: 625px; }

  /* Front */
  .brand-mark {
    position: absolute;
    left: 40px; top: 62px;
    width: 180px;
  }
  .brand-mark__square {
    width: 58px; height: 58px;
    background: var(--green);
    margin-bottom: 18px;
  }
  .brand-mark__name {
    font-family: "Oswald", sans-serif;
    font-weight: 600;
    font-size: 27px;
    line-height: 1.1;
    letter-spacing: .3px;
    color: var(--white);
    text-transform: uppercase;
  }
  .divider-v {
    position: absolute;
    left: 238px; top: 40px;
    width: 1px; height: 160px;
    background: var(--rule);
  }
  .contacts {
    position: absolute;
    left: 254px; top: 36px;
    width: 246px;
  }
  .person { margin-bottom: 8px; }
  .person__name {
    font-family: "Oswald", sans-serif;
    font-weight: 500;
    font-size: 20px;
    line-height: 1.15;
    color: var(--green);
    text-transform: uppercase;
  }
  .line {
    display: flex;
    align-items: center;
    gap: 6px;
    font-size: 14px;
    line-height: 1.3;
    color: var(--text-soft);
    white-space: nowrap;
  }
  .line svg { flex: none; }
  .web-list { margin-top: 14px; }
  .web-list .line { font-size: 13px; margin-bottom: 1px; }
  .divider-h {
    position: absolute;
    height: 1px;
    background: var(--rule);
  }
  .divider-h--top { left: 246px; right: 30px; top: 214px; }
  .divider-h--bottom { left: 40px; right: 30px; top: 272px; }
  .tagline {
    position: absolute;
    left: 40px; right: 30px; top: 230px;
    text-align: center;
    font-weight: 700;
    font-size: 19px;
    letter-spacing: .6px;
    color: var(--green);
    text-transform: uppercase;
  }

  /* Back */
  .back-mark {
    position: absolute;
    top: 58px; left: 0; right: 0;
    display: flex;
    align-items: center;
    justify-content: center;
    gap: 12px;
  }
  .back-mark__square {
    width: 34px; height: 34px;
    background: var(--silver);
  }
  .back-mark__name {
    font-family: "Oswald", sans-serif;
    font-weight: 600;
    font-size: 28px;
    color: var(--silver);
    text-transform: uppercase;
  }
  .services {
    position: absolute;
    left: 30px; right: 30px; top: 150px;
    text-align: center;
  }
  .services__heading {
    display: flex;
    align-items: center;
    gap: 10px;
    font-weight: 700;
    font-size: 15px;
    letter-spacing: .8px;
    color: var(--white);
    text-transform: uppercase;
    margin-bottom: 14px;
  }
  .services__heading::before,
  .services__heading::after {
    content: "";
    flex: 1;
    height: 1px;
    background: var(--rule);
  }
  .services__list {
    list-style: none;
    font-size: 15.5px;
    line-height: 1.4;
    color: var(--text-soft);
  }
</style>
</head>
<body>

<section class="card card--front" aria-label="Card front">
  <div class="brand-mark">
    <div class="brand-mark__square"></div>
    <div class="brand-mark__name">Norrell Advisory</div>
  </div>

  <div class="divider-v"></div>

  <div class="contacts">
    <div class="person">
      <div class="person__name">Derek Holloway</div>
      <div class="line">
        <svg width="9" height="13" viewBox="0 0 9 13"><rect x="1" y="0.75" width="7" height="11.5" rx="1.3" fill="none" stroke="var(--blue)" stroke-width="1.5"/></svg>
        0407385510
      </div>
    </div>
    <div class="person">
      <div class="person__name">Megan Holloway</div>
      <div class="line">
        <svg width="9" height="13" viewBox="0 0 9 13"><rect x="1" y="0.75" width="7" height="11.5" rx="1.3" fill="none" stroke="var(--blue)" stroke-width="1.5"/></svg>
        0407913847
      </div>
    </div>
    <div class="web-list">
      <div class="line">
        <svg width="13" height="10" viewBox="0 0 13 10"><rect x="0.5" y="0.5" width="12" height="9" fill="var(--blue)"/><path d="M0.5 0.5 L6.5 5.5 L12.5 0.5" fill="none" stroke="var(--card)" stroke-width="1.2"/></svg>
        norrelladvisorywa@mailbox-example.com
      </div>
      <div class="line">
        <svg width="13" height="13" viewBox="0 0 13 13"><circle cx="6.5" cy="6.5" r="6" fill="var(--blue)"/><ellipse cx="6.5" cy="6.5" rx="2.5" ry="6" fill="none" stroke="var(--card)" stroke-width="1"/><line x1="0.5" y1="6.5" x2="12.5" y2="6.5" stroke="var(--card)" stroke-width="1"/></svg>
        www.norrelladvisory.com
      </div>
      <div class="line">
        <svg width="13" height="13" viewBox="0 0 13 13"><circle cx="6.5" cy="6.5" r="6" fill="var(--blue)"/></svg>
        social.norrelladvisory.com
      </div>
    </div>
  </div>

  <div class="divider-h divider-h--top"></div>
  <p class="tagline">Small Changes Big Rewards</p>
  <div class="divider-h divider-h--bottom"></div>
</section>

<section class="card card--back" aria-label="Card back">
  <div class="back-mark">
    <div class="back-mark__square"></div>
    <div class="back-mark__name">Norrell Advisory</div>
  </div>

  <div class="services">
    <h2 class="services__heading">Providing Assistance With</h2>
    <ul class="services__list">
      <li>Organisation &amp; Efficiency • Revenue generation &amp; Marketing</li>
      <li>Financial Management • Production quality &amp; delivery</li>
      <li>Systems &amp; Process documentation • Exit Strategy</li>
    </ul>
  </div>
</section>

</body>
</html>
```